LinkedIn Banner Design for B2B Consulting Firm

Take the already developed logo (attached) and incorporate it into a creative banner design for placement on LinkedIn (the social media platform targeting business users). The banner will be used on the firm's company profile page on LinkedIn (not yet created).

```html
<!DOCTYPE html>
<html lang="en">
<head>
<meta charset="UTF-8">
<title>Ridgeline Partners – LinkedIn Banner</title>
<link href="https://fonts.googleapis.com/css2?family=Lato:wght@400;900&display=swap" rel="stylesheet">
<style>
  :root {
    --stage-grey: #dad7d7;
    --banner-white: #ffffff;
    --brand-green: #3d5f45;
    --text-grey: #555a57;
    --photo-light: #d9d6d1;
    --photo-mid: #a7a39c;
    --photo-dark: #3b3a38;
  }
  * { margin: 0; padding: 0; box-sizing: border-box; }
  html, body {
    width: 1200px;
    height: 470px;
    overflow: hidden;
    background: var(--stage-grey);
    font-family: "Lato", sans-serif;
  }
  .banner {
    position: absolute;
    left: 51px;
    top: 142px;
    width: 1098px;
    height: 186px;
    background: var(--banner-white);
    overflow: hidden;
    box-shadow: 0 1px 2px rgba(0,0,0,0.08);
  }
  .headline {
    position: absolute;
    left: 258px;
    top: 42px;
    font-weight: 900;
    font-size: 32px;
    line-height: 33px;
    color: var(--brand-green);
    white-space: nowrap;
  }
  .audience {
    position: absolute;
    left: 259px;
    top: 127px;
    font-weight: 400;
    font-size: 11px;
    color: var(--text-grey);
    white-space: nowrap;
  }
  .brand-name {
    position: absolute;
    left: 582px;
    top: 122px;
    display: flex;
    align-items: center;
    gap: 10px;
    font-weight: 900;
    font-size: 24px;
    line-height: 30px;
    color: var(--brand-green);
    white-space: nowrap;
  }
  .brand-square {
    width: 24px;
    height: 24px;
    background: var(--brand-green);
  }
  .team-photo {
    position: absolute;
    top: 0;
    right: 0;
    width: 400px;
    height: 186px;
    clip-path: polygon(12px 0, 400px 0, 400px 186px, 189px 186px);
    background:
      radial-gradient(ellipse at 70% 60%, rgba(59,58,56,0.55), transparent 60%),
      linear-gradient(100deg, var(--photo-light) 0%, var(--photo-mid) 55%, var(--photo-dark) 100%);
  }
</style>
</head>
<body>
  <section class="banner">
    <h1 class="headline">Fractional&nbsp; Marketing<br>Services to B2B clients</h1>
    <p class="audience">Private Equity Firms, Family Offices, Investment Banks</p>
    <div class="brand-name"><span class="brand-square"></span>Ridgeline Partners</div>
    <div class="team-photo" role="img" aria-label="Photo of business professionals meeting around a table reviewing documents"></div>
  </section>
</body>
</html>
```